Logo and Card design for KRV Home Solutions LLC

I need an edgier logo and business card designs. Current logo attached. I like the colors below. I would like the logo to incorporate a home in the design.
Title = Principal-Acquisitions
Email:KRVHOMESOLUTIONS@fernmail.example
555-214-0937
facebook
IG
2 sided business card with the front being contact info a slogan about selling a home fast. The back incorporating What we do. Buy houses, land, or commercial property as is. We find solutions to make the process of selling simple and fair.

Target Market(s)

Motivated house sellers.

Industry/Entity Type

Business

Contact Information for Business Card

Who we are: We are a Faith based Real Estate Investment Company. We pay cash for homes in any condition and can close quick. Whatever the reason you need to sell fast, we can help. We believe in creating win-win solutions to help you in your time of need. We care! We can help!

Logo Text

KRV Home Solutions LLC

Font styles to use
Sans Serif

Colors
33a6d7
0355a3
85abd2
cee9f5
9d9d9d
b2b2b2
ffffff

Requirements
Must have
• Old logo attached. I want something edgier.
• Company name, phone number, description on the back of what we can do. Pay all cash. Buy in as is condition. No fees,Commisions or closing costs.Close quick. No hassles with solutions to meet your unique situation.
• Call today for an offer within 24 hours.

```html
<!DOCTYPE html>
<html lang="en">
<head>
<meta charset="utf-8">
<title>KRV Home Solutions – Business Card</title>
<link href="https://fonts.googleapis.com/css2?family=Work+Sans:wght@400;500;600&display=swap" rel="stylesheet">
<style>
  :root {
    --navy: #233b7c;
    --navy-deep: #1a2f69;
    --navy-ink: #1f3577;
    --grey-arc: #5b5b5b;
    --white: #ffffff;
    --backdrop: #1b1b1d;
  }
  * { margin: 0; padding: 0; box-sizing: border-box; }
  html, body { width: 1200px; height: 963px; overflow: hidden; }
  body {
    background: var(--backdrop);
    font-family: "Work Sans", sans-serif;
    display: flex;
    flex-direction: column;
    align-items: center;
    justify-content: center;
    gap: 40px;
  }
  .card {
    position: relative;
    width: 760px;
    height: 434px;
    overflow: hidden;
    background: linear-gradient(135deg, var(--navy) 0%, var(--navy-deep) 100%);
    color: var(--white);
  }
  /* Front */
  .card-front .sweep { position: absolute; inset: 0; }
  .contact-block { position: absolute; left: 48px; top: 44px; }
  .company-name {
    font-size: 30px; font-weight: 500; letter-spacing: 1px; text-transform: uppercase;
  }
  .job-title { font-size: 17px; font-weight: 400; margin-top: 4px; letter-spacing: .5px; }
  .divider { width: 46px; height: 2px; background: var(--white); margin: 26px 0 22px; }
  .contact-list { list-style: none; }
  .contact-list li {
    display: flex; align-items: center; gap: 10px;
    font-size: 15px; line-height: 25px; letter-spacing: .3px;
    white-space: nowrap;
  }
  .contact-icon {
    width: 14px; height: 14px; flex: none;
    display: flex; align-items: center; justify-content: center;
  }
  .contact-dot { width: 11px; height: 11px; border-radius: 50%; background: var(--white); }
  .slogan {
    position: absolute; left: 48px; bottom: 40px;
    font-size: 16px; font-weight: 600; letter-spacing: 4px; text-transform: uppercase;
  }
  .front-mark {
    position: absolute; right: 40px; top: 205px; width: 240px; text-align: center;
    color: var(--navy-ink);
  }
  /* Shared brand lockup */
  .brand-name {
    font-size: 38px; font-weight: 600; letter-spacing: 1px; text-transform: uppercase; line-height: 1;
  }
  .brand-sub {
    font-size: 17px; font-weight: 600; letter-spacing: 3px; text-transform: uppercase; margin-top: 6px;
  }
  /* Back */
  .card-back { display: flex; flex-direction: column; align-items: center; justify-content: center; text-align: center; }
  .back-mark { margin-bottom: 34px; }
  .offer-text { font-size: 17px; line-height: 26px; letter-spacing: .6px; max-width: 600px; }
</style>
</head>
<body>

<section class="card card-front" aria-label="Business card front">
  <svg class="sweep" viewBox="0 0 760 434" aria-hidden="true">
    <path d="M580 0 C450 60 400 250 450 434 L760 434 L760 0 Z" fill="var(--white)"/>
    <path d="M565 0 C432 64 384 256 436 434" fill="none" stroke="var(--grey-arc)" stroke-width="12"/>
    <path d="M600 8 C500 60 455 150 445 240" fill="none" stroke="var(--navy-ink)" stroke-width="6" stroke-linecap="round"/>
  </svg>

  <div class="contact-block">
    <h1 class="company-name">KRV Home Solutions</h1>
    <p class="job-title">Principal-Acquisitions</p>
    <div class="divider"></div>
    <ul class="contact-list">
      <li>
        <span class="contact-icon">
          <svg width="14" height="14" viewBox="0 0 24 24" aria-hidden="true"><path fill="#fff" d="M6.6 10.8a15.1 15.1 0 0 0 6.6 6.6l2.2-2.2a1 1 0 0 1 1-.25 11.4 11.4 0 0 0 3.6.57 1 1 0 0 1 1 1V20a1 1 0 0 1-1 1A17 17 0 0 1 3 4a1 1 0 0 1 1-1h3.5a1 1 0 0 1 1 1c0 1.25.2 2.45.57 3.6a1 1 0 0 1-.25 1Z"/></svg>
        </span>555-214-0937
      </li>
      <li><span class="contact-icon"><span class="contact-dot"></span></span>/krvhomesolutions</li>
      <li><span class="contact-icon"><span class="contact-dot"></span></span>@krvhomesolutions</li>
      <li>
        <span class="contact-icon">
          <svg width="14" height="12" viewBox="0 0 24 20" aria-hidden="true"><rect x="1" y="1" width="22" height="18" rx="2" fill="none" stroke="#fff" stroke-width="2"/><path d="M2 3l10 8 10-8" fill="none" stroke="#fff" stroke-width="2"/></svg>
        </span>KRVHOMESOLUTIONS@fernmail.example
      </li>
    </ul>
  </div>

  <p class="slogan">Selling a home fast</p>

  <div class="front-mark">
    <p class="brand-name">KRV Home</p>
    <p class="brand-sub">Solutions</p>
  </div>
</section>

<section class="card card-back" aria-label="Business card back">
  <div class="back-mark">
    <p class="brand-name">KRV Home</p>
    <p class="brand-sub">Solutions</p>
  </div>
  <p class="offer-text">
    Pay all cash. Buy in as is condition. No fees,Commisions<br>
    or closing costs.Close quick. No hassles with solutions<br>
    to meet your unique situation.<br>
    Call today for an offer within 24 hours.
  </p>
</section>

</body>
</html>
```